Alloy wheel repair business needs a website

Install logo previously purchased from makerhive, toolbar with dropdowns. services, gallery, clients , contact ect
Maybe mission statment

Target Market(s)

vehicle owners, auto dealers,insurance companies,

Industry/Entity Type

Alloy Wheel Repair

Coding

Coded - Design and coding required

Number of Pages Required

4 page

Font styles to use
Sans Serif

Colors
0054AA
0677BA
7BADD7
CADEEF
E8F1F8

```html
<!DOCTYPE html>
<html lang="en">
<head>
<meta charset="utf-8">
<title>Rimcraft Works – Alloy Wheel Repair</title>
<link rel="stylesheet" href="https://fonts.googleapis.com/css2?family=Audiowide&family=Montserrat:wght@400;500;600;700;800&display=swap">
<style>
:root{
  --navy:#0054AA;
  --blue:#0677BA;
  --sky:#7BADD7;
  --pale:#CADEEF;
  --mist:#E8F1F8;
  --ink:#111418;
  --dark:#1b1d21;
  --card:#2a2c31;
  --grey:#6b6f76;
  --white:#ffffff;
}
*{box-sizing:border-box;margin:0;padding:0}
html,body{width:1200px;height:4448px;overflow:hidden}
body{font-family:"Montserrat",sans-serif;color:var(--ink);background:var(--white);position:relative}
.abs{position:absolute}
.display{font-family:"Audiowide",sans-serif;text-transform:uppercase;letter-spacing:2px}
.btn{display:inline-block;background:var(--blue);color:var(--white);font-weight:600;font-size:16px;border-radius:24px;padding:12px 30px}
.rule{width:80px;height:4px;background:var(--blue);margin:14px auto 0}
.arrow{position:absolute;width:44px;height:44px;border-radius:50%;display:flex;align-items:center;justify-content:center}
.arrow.grey{background:#8a8d92}
.arrow.blue{background:var(--blue)}

/* header */
.site-header{top:0;left:0;width:1200px;height:72px;background:var(--mist);display:flex;align-items:center;padding:0 40px 0 40px}
.brand{font-weight:800;font-size:30px;color:var(--navy);letter-spacing:1px;text-transform:uppercase}
.main-nav{margin-left:auto;display:flex;gap:26px;align-items:center;font-weight:700;font-size:17px}
.main-nav .btn{font-size:16px;padding:10px 24px}
.info-bar{top:72px;left:0;width:1200px;height:46px;background:#25272b;color:#d8dbe0;font-size:13px;display:flex;align-items:center;justify-content:space-between;padding:0 40px}
.info-bar span{display:flex;align-items:center;gap:8px}

/* hero */
.hero{top:118px;left:0;width:1200px;height:522px;background:radial-gradient(ellipse at 78% 45%,#5a5e66 0%,#2d3036 40%,#141518 80%)}
.hero-copy{top:160px;width:1200px;text-align:center;color:var(--white)}
.hero-copy h1{font-size:44px;line-height:1.3}
.hero-copy .btn{margin-top:36px}
.choose{top:640px;left:0;width:1200px;height:320px;background:linear-gradient(#1c1d20,#232428)}
.choose h2{position:absolute;top:60px;width:1200px;text-align:center;color:var(--white);font-size:30px;line-height:1.5}
.choose-actions{position:absolute;top:256px;left:0;width:1200px;display:flex;justify-content:center;gap:36px}
.pill{display:flex;align-items:center;gap:10px;padding:13px 26px;border-radius:26px;border:2px solid var(--white);color:var(--white);font-weight:600;font-size:16px}
.pill.primary{background:var(--blue);border-color:var(--blue)}

/* about */
.about{top:960px;left:0;width:1200px;height:520px;background:var(--white)}
.about-photo{top:60px;left:120px;width:400px;height:400px;border-radius:50%;background:radial-gradient(circle,#c9ccd1 0%,#7d828a 35%,#2c2e33 62%,#111 100%)}
.about-copy{top:60px;left:608px;width:470px}
.about-copy h2{font-size:38px}
.about-copy .rule{margin:10px 0 0}
.about-copy p{margin-top:28px;font-size:14px;line-height:1.75;color:#444}
.about-copy .btn{margin-top:30px}

/* mission */
.mission{top:1480px;left:0;width:1200px;height:640px;background:radial-gradient(ellipse at 50% 50%,#3b3d42,#1a1b1e 80%)}
.mission h2{position:absolute;top:100px;width:1200px;text-align:center;color:var(--white);font-size:38px}
.mission-card{top:220px;width:462px;height:312px;background:rgba(60,62,68,.85);padding:40px 26px;color:var(--white)}
.mission-card h3{font-size:19px;font-weight:600;margin-top:14px}
.mission-card p{font-size:14px;line-height:1.7;margin-top:8px;color:#e6e7ea}
.mission-card a{display:block;margin-top:8px;color:var(--sky);font-weight:600;font-size:14px;text-decoration:underline}

/* testimonials */
.testimonials{top:2120px;left:0;width:1200px;height:660px;background:var(--white)}
.testimonials h2{position:absolute;top:100px;width:1200px;text-align:center;font-size:38px}
.quote-card{top:272px;left:188px;width:412px;height:256px;background:#3a3a3c;color:var(--white);padding:30px 26px}
.stars{color:#f5b301;font-size:20px;letter-spacing:2px}
.quote-card p{font-size:14px;line-height:1.7;margin-top:8px}
.client{display:flex;align-items:center;gap:12px;margin-top:16px}
.avatar{width:48px;height:48px;border-radius:50%;background:var(--pale)}
.client b{display:block;font-size:15px}
.client small{font-size:12px;color:#ccc}
.quote-mark{top:272px;left:530px;width:56px;height:56px;background:var(--white);border-radius:50%;display:flex;align-items:center;justify-content:center;color:var(--blue);font-size:46px;font-weight:800;line-height:1}
.quote-photo{top:212px;left:600px;width:448px;height:328px;background:linear-gradient(120deg,#1c1c1f 0%,#6b3a22 45%,#2d2f33 100%)}

/* gallery */
.gallery-title{top:2750px;width:1200px;text-align:center;font-size:38px}
.g-img{top:2872px;height:328px}

/* contact band */
.contact-band{top:3340px;left:0;width:1200px;height:532px;background:radial-gradient(ellipse at 50% 40%,#3a3c40,#18191c 80%)}
.contact-item{top:100px;width:320px;text-align:center;color:var(--white);font-size:15px;font-weight:600;line-height:1.6}
.contact-item .ico{width:68px;height:68px;border:3px solid var(--white);border-radius:50%;margin:0 auto 18px;display:flex;align-items:center;justify-content:center}
.footer{top:3872px;left:0;width:1200px;height:576px;background:#000;color:var(--white)}
.form-card{top:3620px;left:92px;width:1016px;height:540px;background:var(--white);padding:56px 44px}
.form-card h2{text-align:center;font-size:38px}
.fields{display:grid;grid-template-columns:1fr 1fr;gap:14px 40px;margin-top:52px}
.field{height:50px;border:1px solid #c8cbd0;border-radius:6px;display:flex;align-items:center;gap:10px;padding:0 14px;font-size:14px;color:#777}
.field.wide{grid-column:1/3;height:76px;align-items:flex-start;padding-top:12px}
.form-card .btn{display:block;width:160px;margin:26px auto 0;text-align:center}

.footer-cols{top:308px;left:112px;width:1000px;display:flex}
.footer-cols h4{font-size:24px;font-weight:700;margin-bottom:22px}
.footer-cols ul{list-style:none;font-size:14px;line-height:1.9}
.footer .brand{color:var(--white);font-size:30px}
.socials{display:flex;gap:14px}
.socials span{width:36px;height:36px;border:2px solid var(--white);border-radius:50%}
.copyright{bottom:0;left:0;width:1200px;height:48px;border-top:1px solid #333;display:flex;align-items:center;justify-content:center;font-size:13px;color:#ccc}
</style>
</head>
<body>

<header class="site-header abs">
  <div class="brand">Rimcraft Works</div>
  <nav class="main-nav">
    <span>Home</span><span>Services</span><span>Gallery</span><span>Clients</span><span>Contact Us</span>
    <span class="btn">Schedule Service</span>
  </nav>
</header>

<div class="info-bar abs">
  <span><svg width="14" height="14" viewBox="0 0 24 24" fill="#fff"><path d="M12 2a7 7 0 0 0-7 7c0 5 7 13 7 13s7-8 7-13a7 7 0 0 0-7-7zm0 9.5A2.5 2.5 0 1 1 12 6.5a2.5 2.5 0 0 1 0 5z"/></svg>Rimcraft Works Lorem Ipsum Lorem Ipsum</span>
  <span><svg width="14" height="14" viewBox="0 0 24 24" fill="none" stroke="#fff" stroke-width="2"><circle cx="12" cy="12" r="9"/><path d="M12 7v5l3 2"/></svg>Mon To Fri 8am to 5pm</span>
  <span><svg width="14" height="14" viewBox="0 0 24 24" fill="#fff"><path d="M6.6 10.8a15 15 0 0 0 6.6 6.6l2.2-2.2a1 1 0 0 1 1-.25 11 11 0 0 0 3.6.6 1 1 0 0 1 1 1V20a1 1 0 0 1-1 1A17 17 0 0 1 3 4a1 1 0 0 1 1-1h3.5a1 1 0 0 1 1 1 11 11 0 0 0 .6 3.6 1 1 0 0 1-.25 1z"/></svg>+1 555 010 2040</span>
</div>

<section class="hero abs" role="img" aria-label="Close-up photograph of a dark sports car alloy wheel">
  <div class="hero-copy abs">
    <h1 class="display">Welcome to<br>Rimcraft Works</h1>
    <span class="btn">Get Started</span>
  </div>
</section>

<section class="choose abs">
  <h2 class="display">A Choose Us For Our Relaible<br>Services</h2>
  <div class="choose-actions">
    <span class="pill primary"><svg width="18" height="18" viewBox="0 0 24 24" fill="none" stroke="#fff" stroke-width="2"><rect x="3" y="5" width="18" height="16" rx="2"/><path d="M3 10h18M8 3v4M16 3v4"/></svg>Schedule Service</span>
    <span class="pill"><svg width="18" height="18" viewBox="0 0 24 24" fill="#fff"><path d="M12 2a7 7 0 0 0-7 7c0 5 7 13 7 13s7-8 7-13a7 7 0 0 0-7-7zm0 9.5A2.5 2.5 0 1 1 12 6.5a2.5 2.5 0 0 1 0 5z"/></svg>Get Direction</span>
    <span class="pill"><svg width="18" height="18" viewBox="0 0 24 24" fill="#fff"><path d="M6.6 10.8a15 15 0 0 0 6.6 6.6l2.2-2.2a1 1 0 0 1 1-.25 11 11 0 0 0 3.6.6 1 1 0 0 1 1 1V20a1 1 0 0 1-1 1A17 17 0 0 1 3 4a1 1 0 0 1 1-1h3.5a1 1 0 0 1 1 1 11 11 0 0 0 .6 3.6 1 1 0 0 1-.25 1z"/></svg>Give Us a Call</span>
    <span class="pill"><svg width="18" height="18" viewBox="0 0 24 24" fill="#fff"><path d="M4 4h16v12H7l-3 3z"/></svg>Contact Us</span>
  </div>
</section>

<section class="about abs">
  <div class="about-photo abs" role="img" aria-label="Photograph of a chrome multi-spoke alloy wheel with tyre"></div>
  <div class="about-copy abs">
    <h2 class="display">About Us</h2>
    <div class="rule"></div>
    <p>Lorem Ipsum is simply dummy text of the printing and typesetting industry. Lorem Ipsum has been the industry's standard dummy text ever since the 1500s, when an unknown printer took a galley of type and scrambled it to make a type specimen book.Lorem Ipsum is simply dummy text of the printing and typesetting industry. Lorem Ipsum has been the industry's standard dummy text ever since the 1500s, when an unknown printer took a galley of type and scrambled it to make a type specimen</p>
    <span class="btn">Read More</span>
  </div>
</section>

<section class="mission abs">
  <h2 class="display">Our Mission</h2>
  <div class="rule abs" style="top:160px;left:560px;margin:0"></div>
  <div class="mission-card abs" style="left:108px">
    <svg width="48" height="48" viewBox="0 0 48 48" fill="none" stroke="#0677BA" stroke-width="4"><circle cx="24" cy="24" r="20"/><circle cx="24" cy="24" r="5"/><path d="M24 19V5M28.8 25.5l13-5M27 28l8 12M21 28l-8 12M19.2 25.5l-13-5"/></svg>
    <h3>Lorem Ipsum</h3>
    <p>Lorem Ipsum is simply dummy text of the printing and typesetting industry. Lorem Ipsum has been the industry's standard dummy text ever since the 1500s, when an unknown printer took a galley of type and scrambled it to make a type specimen book.Lorem</p>
    <a>Read More...</a>
  </div>
  <div class="mission-card abs" style="left:632px">
    <svg width="48" height="48" viewBox="0 0 48 48" fill="none" stroke="#0677BA" stroke-width="4"><circle cx="24" cy="24" r="20"/><circle cx="24" cy="24" r="5"/><path d="M24 19V5M28.8 25.5l13-5M27 28l8 12M21 28l-8 12M19.2 25.5l-13-5"/></svg>
    <h3>Lorem Ipsum</h3>
    <p>Lorem Ipsum is simply dummy text of the printing and typesetting industry. Lorem Ipsum has been the industry's standard dummy text ever since the 1500s, when an unknown printer took a galley of type and scrambled it to make a type specimen book.Lorem</p>
    <a>Read More...</a>
  </div>
  <div class="arrow grey" style="top:358px;left:26px"><svg width="18" height="18" viewBox="0 0 24 24"><path d="M15 4 7 12l8 8" fill="none" stroke="#fff" stroke-width="3"/></svg></div>
  <div class="arrow blue" style="top:358px;left:1114px"><svg width="18" height="18" viewBox="0 0 24 24"><path d="M9 4l8 8-8 8" fill="none" stroke="#fff" stroke-width="3"/></svg></div>
</section>

<section class="testimonials abs">
  <h2 class="display">What Our Clients Say</h2>
  <div class="rule abs" style="top:160px;left:560px;margin:0"></div>
  <div class="quote-photo abs" role="img" aria-label="Photograph of a bronze alloy wheel on a dark car"></div>
  <div class="quote-card abs">
    <div class="stars">★★★★★</div>
    <p>Lorem Ipsum is simply dummy text of the printing and typesetting industry. Lorem Ipsum has been the industry's standard dummy text ever since the 1500s, when an unknown printer took a galley of type and</p>
    <div class="client"><span class="avatar"></span><div><b>Dana</b><small>Client</small></div></div>
  </div>
  <div class="quote-mark abs">“</div>
  <div class="arrow grey" style="top:350px;left:26px"><svg width="18" height="18" viewBox="0 0 24 24"><path d="M15 4 7 12l8 8" fill="none" stroke="#fff" stroke-width="3"/></svg></div>
  <div class="arrow blue" style="top:350px;left:1114px"><svg width="18" height="18" viewBox="0 0 24 24"><path d="M9 4l8 8-8 8" fill="none" stroke="#fff" stroke-width="3"/></svg></div>
</section>

<h2 class="gallery-title abs display">Our Gallery</h2>
<div class="rule abs" style="top:2810px;left:560px;margin:0"></div>
<div class="g-img abs" style="left:108px;width:280px;background:linear-gradient(120deg,#1d1d20,#7a3e22 55%,#2a2b2f)" role="img" aria-label="Photograph of a bronze alloy wheel"></div>
<div class="g-img abs" style="top:2856px;height:364px;left:396px;width:392px;border:6px solid var(--blue);background:linear-gradient(120deg,#24344a,#9aa7b7 50%,#3d4c60)" role="img" aria-label="Photograph of a technician repairing a silver alloy wheel"></div>
<div class="g-img abs" style="left:792px;width:300px;background:linear-gradient(120deg,#e7e3e8,#a23b8c 50%,#3a2234)" role="img" aria-label="Photograph of a wheel being refinished on a machine"></div>
<div class="arrow grey" style="top:3040px;left:26px"><svg width="18" height="18" viewBox="0 0 24 24"><path d="M15 4 7 12l8 8" fill="none" stroke="#fff" stroke-width="3"/></svg></div>
<div class="arrow blue" style="top:3040px;left:1114px"><svg width="18" height="18" viewBox="0 0 24 24"><path d="M9 4l8 8-8 8" fill="none" stroke="#fff" stroke-width="3"/></svg></div>

<section class="contact-band abs">
  <div class="contact-item abs" style="left:110px">
    <div class="ico"><svg width="30" height="30" viewBox="0 0 24 24" fill="#fff"><path d="M6.6 10.8a15 15 0 0 0 6.6 6.6l2.2-2.2a1 1 0 0 1 1-.25 11 11 0 0 0 3.6.6 1 1 0 0 1 1 1V20a1 1 0 0 1-1 1A17 17 0 0 1 3 4a1 1 0 0 1 1-1h3.5a1 1 0 0 1 1 1 11 11 0 0 0 .6 3.6 1 1 0 0 1-.25 1z"/></svg></div>
    +1 555 010 2040
  </div>
  <div class="contact-item abs" style="left:440px">
    <div class="ico"><svg width="30" height="30" viewBox="0 0 24 24" fill="#fff"><path d="M12 2a7 7 0 0 0-7 7c0 5 7 13 7 13s7-8 7-13a7 7 0 0 0-7-7zm0 9.5A2.5 2.5 0 1 1 12 6.5a2.5 2.5 0 0 1 0 5z"/></svg></div>
    500,Rimcraft Works Lorem<br>Ipsum is simply dummy text
  </div>
  <div class="contact-item abs" style="left:770px">
    <div class="ico"><svg width="30" height="30" viewBox="0 0 24 24" fill="none" stroke="#fff" stroke-width="2"><rect x="3" y="5" width="18" height="14" rx="1"/><path d="m3 6 9 7 9-7"/></svg></div>
    support@rimcraftworks.example
  </div>
</section>

<footer class="footer abs">
  <div class="footer-cols abs">
    <div style="width:272px">
      <div class="brand">Rimcraft</div>
      <p style="font-size:14px;line-height:1.7;margin-top:24px;width:230px">Lorem Ipsum is simply dummy text of the printing and typesetting industry. Lorem</p>
    </div>
    <div style="width:228px"><h4>Quick Links</h4><ul><li>Home</li><li>Our Services</li><li>Gallery</li><li>Clients</li><li>Contact Us</li></ul></div>
    <div style="width:300px"><h4>Contact Details</h4><ul><li>+1 555 010 2040</li><li>500,Rimcraft Works Lorem<br>Ipsum is simply dummy text</li><li>support@rimcraft<br>works.example</li></ul></div>
    <div><h4>Follow Us</h4><div class="socials"><span></span><span></span><span></span></div></div>
  </div>
  <div class="copyright abs">© 2023 Rimcraft Works All rights reserved</div>
</footer>

<form class="form-card abs">
  <h2 class="display">Schedule Your Service</h2>
  <div class="rule"></div>
  <div class="fields">
    <div class="field">👤 Name</div>
    <div class="field">✉ Email</div>
    <div class="field">☎ Contact Number</div>
    <div class="field">✎ Subject</div>
    <div class="field wide">Your message</div>
  </div>
  <span class="btn">Submit</span>
</form>

</body>
</html>
```